New Business Card Design for Manufacturing

We are an engineering/manufacturing company that offers Advanced machining/assembly/engineering services, as well as innovative products for the heavy duty engine cooling markets.

We are looking to get a new business card designed that is clean and modern looking, but still fits the wide range of technical/skilled work we do.

- We hope to use this design as the base for other design work in new Presentations, web, and print work.

Industry/Entity Type

Engineering

Contact Information for Business Card

Our preferred color of blue is (RGB) 22/71/159 but can vary slightly from that color. Our content will be our Logo and full company name (Vantrell Forge Works, Inc.), company address, name, job title, phone number with extension, cell number, fax number, website, and email address on the cards.
We'd like the full company name next to the logo, but we are open to other interpretations of that layout.
Preferably, we would like the back side to be clean with just our logo, and the front to contain all of the contact information.

Colors
2f74b4
0355a3
85abd2

Requirements
Must have
• - Logo, company name, needed content - We are open to interpretation beyond that.
• - Standard size business card.
• - Horizontal orientation.
• - Enough space for lengthy names / job titles (for example, a job title could read "Directory of Human Resources" or "V.P. of Governmental Affairs"). We need this to look clean, whether the title be short (CEO) or long (as described above).

```html
<!DOCTYPE html>
<html lang="en">
<head>
<meta charset="utf-8">
<title>Vantrell Forge Works – Business Card</title>
<link href="https://fonts.googleapis.com/css2?family=Open+Sans:wght@400;600;700;800&display=swap" rel="stylesheet">
<style>
  :root {
    --bg: #2a2b2e;
    --blue-deep: #0b3f8f;
    --blue-main: #16479f;
    --blue-bright: #1f66c8;
    --blue-band: #3f8fd3;
    --blue-mid: #2f74b4;
    --rule: #e9eef5;
    --white: #ffffff;
  }
  html, body {
    margin: 0;
    width: 1200px;
    height: 1200px;
    overflow: hidden;
    background: var(--bg);
    font-family: "Open Sans", Arial, sans-serif;
  }
  .canvas {
    width: 1200px;
    height: 1200px;
    display: flex;
    flex-direction: column;
    align-items: center;
    justify-content: center;
    gap: 60px;
  }
  .card {
    position: relative;
    width: 900px;
    height: 514px;
    overflow: hidden;
    color: var(--white);
    box-shadow: 0 14px 30px rgba(0,0,0,.45);
  }

  /* ---------- Front ---------- */
  .card-front {
    background: linear-gradient(135deg, var(--blue-bright) 0%, var(--blue-main) 45%, var(--blue-deep) 100%);
  }
  .edge-tab {
    position: absolute;
    left: 0;
    top: 110px;
    width: 12px;
    height: 96px;
    background: #e8ecf2;
    border-radius: 0 10px 10px 0;
  }
  .brand-lockup {
    position: absolute;
    top: 38px;
    left: 330px;
    display: flex;
    align-items: center;
    gap: 26px;
  }
  .brand-word {
    font-size: 64px;
    font-weight: 800;
    letter-spacing: 1px;
    line-height: 1;
  }
  .brand-fullname {
    font-size: 22px;
    font-weight: 800;
    line-height: 1.05;
    text-transform: uppercase;
    letter-spacing: 1px;
  }
  .brand-fullname small {
    font-size: 11px;
    font-weight: 800;
  }
  .person-name {
    position: absolute;
    left: 120px;
    top: 140px;
    font-size: 36px;
    font-weight: 700;
    margin: 0;
  }
  .divider {
    position: absolute;
    left: 100px;
    right: 0;
    top: 198px;
    height: 4px;
    background: var(--rule);
  }
  .job-title {
    position: absolute;
    left: 120px;
    top: 212px;
    font-size: 17px;
    font-weight: 700;
    margin: 0;
  }
  .contact-list {
    position: absolute;
    left: 120px;
    top: 246px;
    margin: 0;
    padding: 0;
    list-style: none;
    font-size: 13px;
    line-height: 1.45;
  }
  .contact-list li {
    display: flex;
    align-items: center;
    gap: 10px;
  }
  .contact-list .icon {
    width: 14px;
    height: 14px;
    flex: none;
  }
  .contact-list .lines span { display: block; }
  .web-band {
    position: absolute;
    left: 0;
    right: 0;
    bottom: 0;
    height: 70px;
    background: linear-gradient(90deg, var(--blue-band), var(--blue-mid));
    display: flex;
    align-items: center;
    padding-left: 120px;
    font-size: 26px;
    font-weight: 700;
  }

  /* ---------- Back ---------- */
  .card-back {
    background: radial-gradient(ellipse at 45% 40%, var(--blue-bright) 0%, var(--blue-main) 55%, var(--blue-deep) 100%);
  }
  .back-brand {
    position: absolute;
    left: 0;
    right: 0;
    top: 190px;
    text-align: center;
    font-size: 96px;
    font-weight: 800;
    letter-spacing: 2px;
    line-height: 1;
  }
  .back-rule {
    position: absolute;
    left: 0;
    right: 0;
    bottom: 52px;
    height: 6px;
    background: var(--rule);
  }
  .back-band {
    position: absolute;
    left: 0;
    right: 0;
    bottom: 0;
    height: 52px;
    background: linear-gradient(90deg, var(--blue-mid), var(--blue-main));
  }
</style>
</head>
<body>
<main class="canvas">

  <section class="card card-front" aria-label="Business card front">
    <div class="edge-tab"></div>
    <div class="brand-lockup">
      <div class="brand-word">VANTRELL</div>
      <div class="brand-fullname">Vantrell<br>Forge<br>Works <small>INC</small></div>
    </div>

    <h1 class="person-name">Full Name</h1>
    <div class="divider"></div>
    <h2 class="job-title">Office</h2>

    <ul class="contact-list">
      <li>
        <svg class="icon" viewBox="0 0 16 16" aria-hidden="true"><path fill="#fff" d="M4 1 6 5 4.5 6.5a9 9 0 0 0 5 5L11 10l4 2-1 3c-7 0-13-6-13-13z"/></svg>
        <div class="lines"><span>Tel: +1 555 418 2964</span><span>Fax: +1 555 418 3170</span><span>Fax: +1 555 418 3170</span></div>
      </li>
      <li>
        <svg class="icon" viewBox="0 0 16 16" aria-hidden="true"><rect x="1.5" y="3.5" width="13" height="9" fill="none" stroke="#fff" stroke-width="1.6"/><path d="M1.5 3.5 8 9l6.5-5.5" fill="none" stroke="#fff" stroke-width="1.6"/></svg>
        <div class="lines"><span>info@vantrell.org</span></div>
      </li>
      <li>
        <svg class="icon" viewBox="0 0 16 16" aria-hidden="true"><path fill="#fff" d="M8 0a5.5 5.5 0 0 0-5.5 5.5C2.5 10 8 16 8 16s5.5-6 5.5-10.5A5.5 5.5 0 0 0 8 0zm0 8a2.5 2.5 0 1 1 0-5 2.5 2.5 0 0 1 0 5z"/></svg>
        <div class="lines"><span>12/F Ridge House, 88 Alder Road</span><span>Harbor District - Eastport - USA</span></div>
      </li>
    </ul>

    <div class="web-band">www.vantrellforge.com</div>
  </section>

  <section class="card card-back" aria-label="Business card back">
    <div class="back-brand">VANTRELL</div>
    <div class="back-rule"></div>
    <div class="back-band"></div>
  </section>

</main>
</body>
</html>
```